Storm Restoration Contractor needs a professional letterhead design

Looking for a professional letterhead design. Not looking for your cheapo MS Word standard ones that are readily available. Dont want it to be cookie cutter look like ones readily available online. We just recently changed our logo and want to freshen up all our documents. Our company handles restoring a property back to a pre-loss condition after a storm damages it. For example, wind, hail, flood, fire losses.

Target Market(s)

Property Owners, Homeowners, Property Owners, Commercial Property Owners, Property Management Companies

Industry/Entity Type

Construction Company

Requirements
Must have
• Professional, Use 1 of 2 logo options
• Storm Restoration, Roofing, Siding, Windows

```html
<!DOCTYPE html>
<html lang="en">
<head>
<meta charset="utf-8">
<title>Northgate Exteriors Letterhead</title>
<link rel="stylesheet" href="https://fonts.googleapis.com/css2?family=Questrial&display=swap">
<style>
  :root {
    --backdrop: #b9b9b9;
    --paper: #f1f1f1;
    --charcoal: #555354;
    --brand-blue: #2167b0;
    --ink: #2e2e2e;
    --white: #ffffff;
    --footer-band: #cfcfcf;
    --signature-tone: #c9d4ea;
  }
  html, body {
    margin: 0;
    width: 1200px;
    height: 1041px;
    overflow: hidden;
    background: var(--backdrop);
    font-family: "Questrial", "Century Gothic", sans-serif;
  }
  .letterhead {
    position: absolute;
    left: 212px;
    top: 20px;
    width: 800px;
    height: 1032px;
    transform: scale(0.97);
    transform-origin: 0 0;
    background: var(--paper);
    box-shadow: 0 2px 6px rgba(0,0,0,0.35);
    color: var(--ink);
  }
  .header-shapes { position: absolute; left: 0; top: 0; }
  .brand {
    position: absolute;
    left: 60px;
    top: 84px;
    display: flex;
    align-items: center;
    gap: 12px;
    color: var(--white);
  }
  .brand-dot {
    width: 48px; height: 48px;
    border-radius: 50%;
    background: var(--brand-blue);
  }
  .brand-name {
    font-size: 22px;
    line-height: 24px;
    letter-spacing: 1.5px;
    text-transform: uppercase;
  }
  .contact {
    position: absolute;
    top: 90px;
    color: var(--white);
    font-size: 10.5px;
    line-height: 14px;
  }
  .contact-address { left: 449px; }
  .contact-lines { left: 615px; }
  .contact-lines div { display: flex; align-items: center; gap: 6px; }
  .contact-lines svg { width: 11px; height: 11px; }
  .letter-body {
    position: absolute;
    left: 59px;
    top: 238px;
    width: 681px;
    font-size: 11.6px;
    line-height: 14px;
  }
  .letter-body p { margin: 0 0 14px; text-align: justify; }
  .date { margin-bottom: 14px !important; }
  .recipient { margin-bottom: 54px !important; text-align: left !important; }
  .salutation { font-weight: bold; }
  .closing { display: flex; align-items: flex-start; gap: 16px; margin-top: 22px; }
  .signer { font-weight: bold; }
  .signature {
    width: 170px; height: 80px;
    margin-top: -22px;
    background: var(--signature-tone);
    border-radius: 6px;
  }
  .footer-band {
    position: absolute;
    left: 0; bottom: 0;
    width: 800px; height: 20px;
    background: var(--footer-band);
  }
</style>
</head>
<body>
  <main class="letterhead">
    <svg class="header-shapes" width="800" height="160" viewBox="0 0 800 160" aria-hidden="true">
      <polygon points="0,0 390,0 333,158 0,158" fill="var(--charcoal)"/>
      <polygon points="373,65 800,65 800,158 339,158" fill="var(--brand-blue)"/>
    </svg>

    <div class="brand">
      <span class="brand-dot"></span>
      <div class="brand-name">Northgate<br>Exteriors</div>
    </div>

    <div class="contact contact-address">
      <div>NORTHGATE EXTERIORS</div>
      <div>4120 E Canyon Ridge Rd STE 204</div>
      <div>Mesa, AZ 85201</div>
    </div>

    <div class="contact contact-lines">
      <div>
        <svg viewBox="0 0 12 12"><rect width="12" height="12" rx="2" fill="var(--white)"/><path d="M3.5 2.5l1.5 0 .6 2-1 .8a5 5 0 0 0 2.1 2.1l.8-1 2 .6v1.5a1 1 0 0 1-1 1A6 6 0 0 1 2.5 3.5a1 1 0 0 1 1-1z" fill="var(--brand-blue)"/></svg>
        <span>480-555-0142</span>
      </div>
      <div>
        <svg viewBox="0 0 12 12"><rect width="12" height="12" rx="2" fill="var(--white)"/><rect x="2.5" y="3.5" width="7" height="5" fill="none" stroke="var(--brand-blue)"/><path d="M2.5 3.5l3.5 3 3.5-3" fill="none" stroke="var(--brand-blue)"/></svg>
        <span>info@northgateext.com</span>
      </div>
      <div>
        <svg viewBox="0 0 12 12"><rect width="12" height="12" rx="2" fill="var(--white)"/><circle cx="6" cy="6" r="3.5" fill="none" stroke="var(--brand-blue)"/><path d="M2.5 6h7M6 2.5v7" stroke="var(--brand-blue)"/></svg>
        <span>www.northgateext.com</span>
      </div>
    </div>

    <section class="letter-body">
      <p class="date">30.09.2016</p>
      <p class="recipient">Recipient's name<br>Lindenweg 14<br>10115 Berlin<br>Germany</p>
      <p class="salutation">Dear sir,</p>
      <p>Communication is a very integral part of living creatures, animals and humans. Communication may be verbal or written. Written communication however is only applicable to human beings. Can you even imagine a world without communication? Verbal communication can be through telephones, webcams or in person. Written communication is through letters, emails and mobile phone messages.</p>
      <p>In today's world of great inventions and technology, letters have somehow become redundant. It is the time for text messages or chats. But they still can communicate a lot more than all other modes of communication. Organizations and various government departments still bank on letters as a strong medium of communication. There is no comparison in costs of sending letters as compared to costs of mobile phone messages though – letters are far cheaper. Letters now commonly known as “hard copy documents” are considered more relevant and important than email copies of text messages as proof or evidence of some sort.</p>
      <p>Letters speak volumes about a person or an organization that writes it. So one must take utmost care ensuring that the language used in any letter is appropriate for the occasion for which it is being written. Since a letter is also a written proof or document, if there are certain things that should not form a part of it, then that too should be carefully handled.</p>
      <p>Writing a good letter is an art. But if for some reason someone is unable to write that perfect letter, these different types of letters provide a base for you to build on. Sample letters have been given for everyone to understand what all information needs to form a part of the letter type and then it can be customized.</p>
      <div class="closing">
        <div>Yours Sincerely,<br><span class="signer">Dana Whitlock</span></div>
        <div class="signature" role="img" aria-label="Handwritten signature of Dana Whitlock"></div>
      </div>
    </section>

    <div class="footer-band"></div>
  </main>
</body>
</html>
```